Request for Business Card Design

Hi. My name is Marlene, I am looking for a new business card design for my company, Quarrow Signal Instruments, LLC. I really like the design you did for Tarsel Venture and was hoping you could do something similar using our full logo and our mark. I am also open to any raised texture design using our mark. I have attached our full logo, which would need to be somewhere on the card, as well as the mark in both outline and full form, as well as our brand colors / guide. The card does not have to be white, as long as our logo and mark appear. I actually like darker colored business cards more, but am open to all options. If you are interested in working with me, please let me know. We would also take the business card design into letterhead design if you can do that.

```html
<!DOCTYPE html>
<html lang="en">
<head>
<meta charset="utf-8">
<title>Quarrow Signal Instruments – Business Card</title>
<link rel="stylesheet" href="https://fonts.googleapis.com/css2?family=Barlow:wght@500;600;700&family=Poppins:wght@400;500&display=swap">
<style>
  :root {
    --stage: #2b2b2d;
    --card-dark: #1c1d1f;
    --brand-blue: #0ea5cf;
    --brand-blue-light: #2ec4ec;
    --brand-blue-deep: #0a8fb8;
    --ink-white: #ffffff;
    --rule: #6b6d70;
  }
  * { box-sizing: border-box; margin: 0; padding: 0; }
  html, body { width: 1200px; height: 1108px; overflow: hidden; background: var(--stage); }
  .stage { position: relative; width: 1200px; height: 1108px; }

  .card {
    position: absolute;
    top: 214px;
    width: 390px;
    height: 680px;
    border-radius: 26px;
    overflow: hidden;
  }
  .card--front { left: 170px; background: var(--card-dark); color: var(--ink-white); text-align: center; }
  .card--back { left: 640px; }

  .brand { position: absolute; top: 120px; left: 0; right: 0; }
  .brand__dot {
    width: 64px; height: 64px; border-radius: 50%;
    background: var(--brand-blue); margin: 0 auto 26px;
  }
  .brand__name {
    font-family: "Barlow", sans-serif; font-weight: 700;
    font-size: 58px; letter-spacing: 6px; line-height: 1;
  }
  .brand__tagline {
    font-family: "Barlow", sans-serif; font-weight: 700;
    font-size: 14.5px; letter-spacing: 1.6px; margin-top: 8px;
  }

  .person { position: absolute; top: 372px; left: 0; right: 0; }
  .person__name {
    font-family: "Barlow", sans-serif; font-weight: 600;
    font-size: 31px; color: var(--brand-blue); letter-spacing: 0.5px; line-height: 1;
  }
  .person__title {
    font-family: "Barlow", sans-serif; font-weight: 500;
    font-size: 17px; letter-spacing: 1px; margin-top: 4px;
  }

  .icon-row {
    position: absolute; top: 454px; left: 40px; right: 40px;
    display: flex; align-items: center; gap: 8px;
  }
  .icon-row__rule { flex: 1; height: 1px; background: var(--rule); }
  .icon-row__icon {
    width: 30px; height: 30px; border-radius: 5px;
    background: var(--brand-blue);
    display: flex; align-items: center; justify-content: center;
  }

  .contact {
    position: absolute; top: 500px; left: 0; right: 0;
    font-family: "Poppins", sans-serif; font-size: 17px; line-height: 1.45;
  }
  .contact__rule {
    position: absolute; top: 588px; left: 60px; right: 60px;
    height: 1px; background: var(--rule);
  }
  .address {
    position: absolute; top: 604px; left: 0; right: 0;
    font-family: "Poppins", sans-serif; font-size: 16px; line-height: 1.4;
  }

  .back__pattern {
    position: absolute; inset: 0;
    background: linear-gradient(215deg, var(--brand-blue-light) 0%, var(--brand-blue) 45%, var(--brand-blue-deep) 100%);
  }
  .back__brand {
    position: absolute; left: 250px; top: 470px;
    display: flex; align-items: center; gap: 8px;
    font-family: "Barlow", sans-serif; font-weight: 700;
    font-size: 20px; letter-spacing: 1.5px; color: var(--ink-white);
  }
  .back__brand-dot { width: 14px; height: 14px; border-radius: 50%; background: var(--ink-white); }
</style>
</head>
<body>
<main class="stage">

  <section class="card card--front" aria-label="Business card front">
    <header class="brand">
      <div class="brand__dot"></div>
      <h1 class="brand__name">QUARROW</h1>
      <p class="brand__tagline">SIGNAL INSTRUMENTS</p>
    </header>

    <div class="person">
      <h2 class="person__name">MARLENE HADLEY</h2>
      <p class="person__title">MANAGING DIRECTOR</p>
    </div>

    <div class="icon-row">
      <span class="icon-row__rule"></span>
      <span class="icon-row__icon" aria-label="Phone">
        <svg width="18" height="18" viewBox="0 0 24 24"><path fill="#1c1d1f" d="M6.6 10.8a15 15 0 0 0 6.6 6.6l2.2-2.2a1 1 0 0 1 1-.25 11.4 11.4 0 0 0 3.6.57 1 1 0 0 1 1 1V20a1 1 0 0 1-1 1A17 17 0 0 1 3 4a1 1 0 0 1 1-1h3.5a1 1 0 0 1 1 1c0 1.25.2 2.45.57 3.57a1 1 0 0 1-.25 1z"/></svg>
      </span>
      <span class="icon-row__icon" aria-label="Email">
        <svg width="18" height="18" viewBox="0 0 24 24"><rect x="3" y="6" width="18" height="12" fill="none" stroke="#1c1d1f" stroke-width="2"/><path d="M3 6l9 7 9-7" fill="none" stroke="#1c1d1f" stroke-width="2"/></svg>
      </span>
      <span class="icon-row__icon" aria-label="Website">
        <svg width="18" height="18" viewBox="0 0 24 24"><circle cx="12" cy="12" r="9" fill="none" stroke="#1c1d1f" stroke-width="2"/><path d="M3 12h18M12 3c3 3 3 15 0 18M12 3c-3 3-3 15 0 18" fill="none" stroke="#1c1d1f" stroke-width="1.6"/></svg>
      </span>
      <span class="icon-row__rule"></span>
    </div>

    <address class="contact" style="font-style: normal;">
      <p>044-318 702 546</p>
      <p>hello@quarrowsignal.com</p>
      <p>www.quarrowsignal.com</p>
    </address>
    <div class="contact__rule"></div>
    <address class="address" style="font-style: normal;">
      <p>87, Fenwick Quay Road</p>
      <p>30917, Larmont</p>
    </address>
  </section>

  <section class="card card--back" aria-label="Business card back">
    <div class="back__pattern" role="img" aria-label="Raised repeating brand mark texture in blue tones"></div>
    <div class="back__brand">
      <span class="back__brand-dot"></span>
      <span>QUARROW</span>
    </div>
  </section>

</main>
</body>
</html>
```